Dovecote Realty

Business cards for 4 people

They need to say for all
87 Tarrow Quay, Boston MA 02114

Each person will have their own personal information
We would like gold embossing for the name of the company
Marla is the blonde sitting in the chair smiling her information should be on the back of the card with her name and information
Should say for slogan classic pattern, elevated experience
grace@dovecoteprops.com
(413) 555-0182

Odette is the brunette with wavy hair in the tan suit celina@dovecoteprops.com
(617) 555-0137

sabine@dovecoteprops.com
(413) 555-0164
standing next to the chair

hope@dovecoteprops.com
(413) 555-0199
close up headshot

```html
<!DOCTYPE html>
<html lang="en">
<head>
<meta charset="utf-8">
<title>Dovecote Realty — Business Card</title>
<link href="https://fonts.googleapis.com/css2?family=Cinzel:wght@500&family=Montserrat:wght@700&family=Arimo:wght@400&display=swap" rel="stylesheet">
<style>
  :root {
    --backdrop: #3e5f7d;
    --card-navy: #1c3461;
    --gold: #c9a24f;
    --photo-light: #d9d6d1;
    --photo-warm: #9a8064;
    --text-light: #ffffff;
  }
  * { margin: 0; padding: 0; box-sizing: border-box; }
  html, body {
    width: 1200px;
    height: 1200px;
    overflow: hidden;
    background: var(--backdrop);
  }
  .canvas {
    width: 1200px;
    height: 1200px;
    display: flex;
    align-items: center;
    justify-content: center;
  }
  .business-card {
    position: relative;
    width: 1050px;
    height: 600px;
    background: var(--card-navy);
    overflow: hidden;
    box-shadow: 0 20px 40px rgba(0, 0, 0, 0.25);
  }
  .portrait-shape {
    position: absolute;
    inset: 0;
    width: 1050px;
    height: 600px;
  }
  .card-info {
    position: absolute;
    left: 470px;
    right: 40px;
    top: 70px;
    display: flex;
    flex-direction: column;
    align-items: center;
    text-align: center;
  }
  .brand-mark {
    width: 120px;
    height: 120px;
    border: 3px solid var(--gold);
    border-radius: 50%;
    margin-bottom: 26px;
  }
  .brand-name {
    font-family: "Cinzel", serif;
    font-weight: 500;
    color: var(--gold);
    font-size: 50px;
    line-height: 1;
    letter-spacing: 1px;
  }
  .brand-sub {
    font-family: "Cinzel", serif;
    font-weight: 500;
    color: var(--gold);
    font-size: 16px;
    letter-spacing: 14px;
    margin-top: 8px;
    padding-left: 14px;
  }
  .agent-name {
    font-family: "Montserrat", sans-serif;
    font-weight: 700;
    color: var(--gold);
    font-size: 40px;
    letter-spacing: 14px;
    padding-left: 14px;
    margin-top: 56px;
    margin-bottom: 14px;
  }
  .contact-line {
    font-family: "Arimo", sans-serif;
    color: var(--text-light);
    font-size: 28px;
    line-height: 1.3;
  }
</style>
</head>
<body>
  <main class="canvas">
    <article class="business-card">
      <svg class="portrait-shape" viewBox="0 0 1050 600" xmlns="http://www.w3.org/2000/svg">
        <defs>
          <linearGradient id="portraitTone" x1="0" y1="0" x2="0.4" y2="1">
            <stop offset="0" stop-color="#d9d6d1"/>
            <stop offset="0.55" stop-color="#c9c2b8"/>
            <stop offset="1" stop-color="#9a8064"/>
          </linearGradient>
        </defs>
        <circle cx="88" cy="330" r="352" fill="url(#portraitTone)" role="img"
          aria-label="Portrait photo of the agent standing beside an upholstered chair, wearing a tan suit and white shirt"/>
        <circle class="portrait-ring" cx="88" cy="330" r="354" fill="none" stroke="#c9a24f" stroke-width="6"/>
      </svg>

      <div class="card-info">
        <div class="brand-mark"></div>
        <div class="brand-name">DOVECOTE</div>
        <div class="brand-sub">REALTY</div>
        <div class="agent-name">SABINE</div>
        <div class="contact-line">(413) 555-0164</div>
        <div class="contact-line">sabine@dovecoteprops.com</div>
        <div class="contact-line">87 Tarrow Quay, Boston MA 02114</div>
      </div>
    </article>
  </main>
</body>
</html>
```